Flyer-Design für psychologische Beratungspraxis für Mütter
Vielen herzlichen Dank! Super Kommunikation, alle Änderungswünsche wurden sofort umgesetzt, auch hin und her meinerseits war kein Problem, immer wieder. Schnelle Reaktion, tolle Ideen. Ich bin super zufrieden und würde jederzeit sehr gerne wieder mit brightfoxes zusammenarbeiten! Toller Flyer, ich liebe meinen neuen Flyer! :)
Zielgruppe
Mareva Praxis ist eine psychologische Beratungspraxis. Ich unterstütze Mütter, Schwangere und Frauen mit Kinderwunsch bei Herausforderungen rund um Schwangerschaft, Geburt, Mutterschaft, und damit einhergehenden Problemen.
Aufgabenstellung
Text nochmal geringgradig geändert...siehe Datei anbei

```html
<!DOCTYPE html>
<html lang="de">
<head>
<meta charset="utf-8">
<title>Flyer Krisenbegleitung und Lebensberatung</title>
<link href="https://fonts.googleapis.com/css2?family=Poppins:wght@400;600;700&family=Amatic+SC:wght@700&display=swap" rel="stylesheet">
<style>
  :root{
    --bg:#e8e8e6;
    --paper:#ffffff;
    --paper-inner:#eef0ec;
    --navy:#1f2b8c;
    --pill:#ecedf0;
    --highlight:#b9cbe6;
    --photo-warm-1:#e9b27a;
    --photo-warm-2:#a85a22;
    --photo-warm-3:#3a2418;
    --sky:#dcdad6;
  }
  *{box-sizing:border-box;margin:0;padding:0}
  html,body{width:1200px;height:864px;overflow:hidden;background:var(--bg)}
  body{position:relative;font-family:"Poppins",Arial,sans-serif;color:var(--navy)}

  .spread{position:absolute;left:40px;top:22px;width:820px;height:410px;display:flex;box-shadow:0 6px 24px rgba(0,0,0,.12)}
  .panel{position:relative;width:410px;height:410px;overflow:hidden}
  .panel--left{background:var(--paper-inner)}
  .panel--right{background:var(--paper)}

  .mother-photo{position:absolute;left:190px;top:22px;width:170px;height:170px}

  .intro{position:absolute;left:24px;top:196px;width:360px;font-size:8px;line-height:1.4}
  .intro p{margin-bottom:7px}
  .intro strong{font-weight:700}
  .marker{background:var(--highlight);border-radius:8px;padding:0 5px;font-weight:700;white-space:nowrap}

  .heading-pill{position:absolute;left:18px;top:18px;background:var(--pill);border-radius:14px;padding:4px 16px 4px 14px;font-weight:600;font-size:17px;letter-spacing:.5px}
  .text-column{position:absolute;left:22px;top:60px;width:370px;font-size:7.8px;line-height:1.38}
  .questions{list-style:none;margin-bottom:12px}
  .questions li{padding-left:8px;text-indent:-8px}
  .questions strong,.closing strong{font-weight:700}
  .closing{width:280px;line-height:1.4}
  .closing p{margin-bottom:7px}
  .silhouette{position:absolute;right:16px;bottom:18px;width:78px;height:200px;border-radius:40px 40px 10px 10px;background:linear-gradient(180deg,#5a5a5a,#2e2e2e)}

  .cover{position:absolute;left:760px;top:440px;width:410px;height:410px;overflow:hidden;box-shadow:0 6px 24px rgba(0,0,0,.14)}
  .cover-photo{position:absolute;inset:0;background:linear-gradient(180deg,var(--sky) 0%,var(--sky) 22%,var(--photo-warm-1) 40%,var(--photo-warm-2) 68%,var(--photo-warm-3) 100%)}
  .cover-title{position:absolute;right:18px;top:40px;text-align:right}
  .title-pill{display:inline-block;background:#fff;border-radius:18px;padding:2px 16px;font-family:"Amatic SC",cursive;font-weight:700;font-size:27px;letter-spacing:.5px;color:var(--navy)}
  .subtitle-pill{display:inline-block;margin-top:6px;background:rgba(255,255,255,.92);border-radius:14px;padding:4px 14px;font-size:10px;line-height:1.35;color:var(--navy);text-align:center}
  .brand{position:absolute;right:22px;bottom:22px;color:#fff;font-size:9px;font-weight:600;letter-spacing:.3px}
</style>
</head>
<body>

<section class="spread">
  <div class="panel panel--left">
    <svg class="mother-photo" viewBox="0 0 170 170" role="img" aria-label="Gemalte Illustration: Mutter mit Neugeborenem">
      <defs>
        <linearGradient id="photoTone" x1="0" y1="0" x2="1" y2="1">
          <stop offset="0" stop-color="#9ec6cf"/>
          <stop offset=".5" stop-color="#c9a78a"/>
          <stop offset="1" stop-color="#4a3426"/>
        </linearGradient>
      </defs>
      <path d="M20 60 C25 25 70 15 100 28 C135 40 160 75 150 115 C140 150 95 165 60 150 C25 135 15 95 20 60 Z" fill="url(#photoTone)"/>
      <path d="M130 8 C150 40 162 80 158 110" fill="none" stroke="var(--navy)" stroke-width="1.6"/>
      <path d="M120 158 C140 156 160 150 170 142" fill="none" stroke="var(--navy)" stroke-width="1.6"/>
    </svg>

    <div class="intro">
      <p><strong>Mutter sein ist wunderbar.</strong> Wenn eine Frau Mutter wird, ist sie plötzlich verliebt über beide Ohren, unbändig stolz und von Glücksgefühlen völlig überwältigt. <strong>So ist es doch NORMAL, oder...?</strong></p>
      <p><strong>Überforderung, Frustration</strong> und <strong>Verzweiflung</strong> kennen Mütter, Frauen mit Kinderwunsch und werdende Mütter allerdings ebenfalls nur zu gut. Wichtig ist, dass die Beurteilung einer Situation, d.h. wie stark sie uns belastet, alleine uns selbst zusteht. Nur unsere eigene <strong>subjektive Einschätzung</strong> ist ausschlaggebend.</p>
      <p>So unterschiedlich wir Menschen sind, so verschieden ist auch unser persönliches Fühlen und Erleben. Deshalb benötigen wir <strong>individuell passende Lösungen</strong> für unsere Herausforderungen.</p>
      <p>Ja, Mutter sein ist wundervoll! Und ja, die Dynamik der Paarbeziehung verändert sich schlagartig und wir stehen plötzlich vor einer der erfüllendsten Aufgaben und zugleich einer der größten <strong>existentiellen Herausforderungen</strong>, die uns das Leben bietet: <span class="marker">Eltern sein.</span></p>
    </div>
  </div>

  <div class="panel panel--right">
    <h2 class="heading-pill">WENN ALSO...</h2>
    <div class="text-column">
      <ul class="questions">
        <li>... wir <strong>gern Mutter wären</strong> aber das Leben andere Pläne hat?</li>
        <li>... uns die Erfahrung der <strong>Geburt belastet</strong>, aber niemand zuhört, weil ja „jetzt alles ok ist“?</li>
        <li>... wenn wir unser <strong>Kind verloren</strong> haben?</li>
        <li>... unser Kind oder wir selbst mit einer <strong>Krankheit</strong> zu kämpfen haben?</li>
        <li>... wir selbst oder unser Partner uns <strong>kaum wiedererkennen?</strong></li>
        <li>... wenn wir uns treu bleiben wollen, aber uns dennoch durch die Meinung anderer <strong>verunsichern</strong> lassen?</li>
        <li>... wir eben <strong>nicht stolz</strong> darauf sind, wie wir den letzten Schreianfall unseres Babys begleitet haben?</li>
        <li>... wir weder die Wut unseres Kindes, noch unsere eigene <strong>Wut</strong> gebändigt bekommen?</li>
        <li>... wir mit der Situation <strong>überfordert</strong> sind und nicht mehr weiter wissen?</li>
      </ul>
      <div class="closing">
        <p>Um trotz Rückschlägen ein zufriedenes Leben zu führen und um feinfühlig für unsere Kinder da zu sein, benötigen wir viel Kraft. Mentale Kraft, die es uns ermöglicht, aus den Augen unserer Kinder zu sehen, unsere eigenen Gefühle zu regulieren und die starken Gefühle unserer Kinder auszuhalten und zu begleiten.</p>
        <p>Gemeinsam erarbeiten wir <strong>individuelle Strategien</strong>, wie Sie auf Ihre eigenen Ressourcen besser zugreifen und so mental gestärkt nach vorne schauen können.</p>
      </div>
    </div>
    <div class="silhouette" role="img" aria-label="Silhouette einer stehenden Frau"></div>
  </div>
</section>

<section class="cover">
  <div class="cover-photo" role="img" aria-label="Foto: Mutter hält ihr Kind im warmen Abendlicht"></div>
  <div class="cover-title">
    <h1 class="title-pill">KRISENBEGLEITUNG UND LEBENSBERATUNG</h1><br>
    <p class="subtitle-pill">für Mütter, Schwangere und<br>Frauen mit Kinderwunsch</p>
  </div>
  <div class="brand">Mareva Praxis</div>
</section>

</body>
</html>
```